Commercial Refrigeration Service Company requires stylish and fresh looking flyer.

We need a flyer to hand out to new customers. It should have a photo and our branding, list all the services that are offered and our contact details.
We would like two flyers to be supplied, both identical though one offering a discount until July ( Half Price Service Fee ). The flyer should be clear, interesting and in similar colours to the branding package supplied.
Please look at our website for information about the services on offer:
www.brisko-coolworks.com.au

Target Market(s)

Cafes, bars, restaurants, pubs ect.

Font styles to use
Other font styles liked:
• Font package provided

Colors
85cae6
ffffff
333333

Requirements
Must have
• - The photo provided.
• - The company logo.
• - Similar feel to the website & business card.
• - Smooth layout and clear to understand.
Should not have
• - No clunky badges or prints.

```html
<!DOCTYPE html>
<html lang="en">
<head>
<meta charset="utf-8">
<title>Brisko Commercial Refrigeration Flyer</title>
<link rel="stylesheet" href="https://fonts.googleapis.com/css2?family=Oswald:wght@500&family=Montserrat:wght@300;400;600;800&family=Josefin+Sans:wght@300&display=swap">
<style>
  :root {
    --brand-blue: #56bde6;
    --accent-blue: #4fb9e3;
    --ink: #333333;
    --white: #ffffff;
    --panel-grey: #5a626a;
    --paper: #e9e9e9;
    --stage: #555555;
  }
  * { margin: 0; padding: 0; box-sizing: border-box; }
  html, body { width: 1200px; height: 1146px; overflow: hidden; background: var(--stage); }
  .flyer {
    position: absolute; left: 209px; top: 20px;
    width: 781px; height: 1106px;
    background: var(--paper); overflow: hidden;
    font-family: "Montserrat", sans-serif; color: var(--ink);
  }
  .hero {
    position: absolute; left: 0; top: 0; width: 781px; height: 592px;
    background: var(--panel-grey);
  }
  .hero-photo {
    position: absolute; left: 0; top: 0; width: 781px; height: 592px;
    background:
      linear-gradient(90deg, rgba(90,98,106,0) 0%, rgba(90,98,106,0) 42%, rgba(90,98,106,1) 58%),
      linear-gradient(180deg, #9fc0d8 0%, #b9cfdc 12%, #7b7f88 22%, #6d717a 55%, #8b8d90 75%, #6f7073 100%);
  }
  .services { position: absolute; left: 0; top: 0; width: 781px; height: 592px; }
  .services-title {
    position: absolute; left: 525px; top: 30px;
    font-family: "Montserrat", sans-serif; font-weight: 800; font-size: 23px;
    color: var(--accent-blue); letter-spacing: 0.2px;
  }
  .service-rail { position: absolute; left: 0; top: 0; }
  .service-name {
    position: absolute; left: 525px;
    font-family: "Oswald", sans-serif; font-weight: 500; font-size: 20px;
    color: var(--white); line-height: 1; transform: translateY(-50%);
    text-transform: uppercase; letter-spacing: 0.1px;
  }
  .brand-band {
    position: absolute; left: 0; top: 592px; width: 781px; height: 158px;
    background: var(--brand-blue);
  }
  .brand-name {
    position: absolute; left: 0; right: 0; top: 22px; text-align: center;
    font-family: "Josefin Sans", sans-serif; font-weight: 300; font-size: 52px;
    letter-spacing: 38px; padding-left: 38px; color: var(--ink);
  }
  .brand-dot {
    position: absolute; left: 379px; top: 105px; width: 22px; height: 22px;
    border: 1.5px solid var(--ink); border-radius: 50%;
  }
  .details { position: absolute; left: 0; top: 750px; width: 781px; height: 356px; text-align: center; }
  .tagline-top {
    position: absolute; left: 0; right: 0; top: 16px;
    font-size: 12px; letter-spacing: 4px; font-weight: 400;
    display: flex; justify-content: center; align-items: center; gap: 14px;
  }
  .tagline-top::before, .tagline-top::after {
    content: ""; width: 28px; height: 1px; background: var(--ink);
  }
  .tagline-main {
    position: absolute; left: 0; right: 0; top: 40px;
    font-size: 21px; letter-spacing: 10px; padding-left: 10px; font-weight: 400;
  }
  .diamonds { position: absolute; left: 0; width: 781px; height: 16px; }
  .contact {
    position: absolute; left: 0; right: 0; top: 132px;
    font-size: 16.5px; line-height: 20.5px; font-weight: 400; letter-spacing: -0.3px;
  }
  .website {
    position: absolute; left: 0; right: 0; top: 249px;
    font-size: 17.5px; font-weight: 600; letter-spacing: 3.2px; color: var(--accent-blue);
  }
  .social { position: absolute; left: 0; top: 288px; width: 781px; height: 26px; }
</style>
</head>
<body>
  <div class="flyer">
    <section class="hero">
      <div class="hero-photo" role="img" aria-label="Photo of the technician leaning against the company service ute in a car park"></div>
      <div class="services">
        <h2 class="services-title">SERVICES</h2>
        <svg class="service-rail" width="781" height="592" viewBox="0 0 781 592">
          <line x1="480" y1="111" x2="480" y2="507" stroke="#ffffff" stroke-width="2"/>
          <g fill="#56bde6" stroke="#ffffff" stroke-width="2">
            <circle cx="480" cy="111" r="23"/>
            <circle cx="480" cy="177" r="23"/>
            <circle cx="480" cy="243" r="23"/>
            <circle cx="480" cy="309" r="23"/>
            <circle cx="480" cy="376" r="23"/>
            <circle cx="480" cy="442" r="23"/>
            <circle cx="480" cy="507" r="23"/>
          </g>
          <g fill="none" stroke="#ffffff" stroke-width="1.6" stroke-linecap="round" stroke-linejoin="round">
            <!-- thermometer -->
            <path d="M477 99 v16 a6 6 0 1 0 6 0 v-16 a3 3 0 0 0 -6 0z"/>
            <path d="M486 101 h4 M486 105 h3 M486 109 h4"/>
            <!-- glass -->
            <path d="M470 167 h20 l-3 20 h-14z"/>
            <path d="M471 174 h18"/>
            <!-- tap -->
            <path d="M472 237 h12 v-6 M484 237 v8 h-5 v6 M476 245 h-4 v-8"/>
            <!-- bolt -->
            <path d="M484 296 l-10 15 h7 l-3 12 l10 -16 h-7z"/>
            <!-- tools -->
            <path d="M469 387 l22 -22 M491 387 l-22 -22 M488 368 l4 -4 M468 368 a4 4 0 1 0 4 -4"/>
            <!-- cart -->
            <path d="M467 433 h4 l3 13 h14 l3 -9 h-18"/>
            <circle cx="476" cy="450" r="1.8"/>
            <circle cx="486" cy="450" r="1.8"/>
            <!-- pencil & ruler -->
            <path d="M469 518 l18 -18 l4 4 l-18 18 h-4z M469 496 l22 22"/>
          </g>
        </svg>
        <p class="service-name" style="top:111px">Commercial Refrigeration</p>
        <p class="service-name" style="top:177px">Ice Makers</p>
        <p class="service-name" style="top:243px">Beer Systems</p>
        <p class="service-name" style="top:309px">Electrical</p>
        <p class="service-name" style="top:376px">24hr Service</p>
        <p class="service-name" style="top:442px">Sales</p>
        <p class="service-name" style="top:507px">Installation</p>
      </div>
    </section>

    <section class="brand-band">
      <h1 class="brand-name">BRISKO</h1>
      <span class="brand-dot"></span>
    </section>

    <section class="details">
      <p class="tagline-top">COMMERCIAL</p>
      <p class="tagline-main">REFRIGERATION</p>
      <svg class="diamonds" style="top:97px" viewBox="0 0 781 16">
        <g fill="none" stroke="#4fb9e3" stroke-width="2">
          <path d="M353 8 l5 -5 l5 5 l-5 5z"/>
          <path d="M385 8 l5 -5 l5 5 l-5 5z"/>
          <path d="M418 8 l5 -5 l5 5 l-5 5z"/>
        </g>
      </svg>
      <p class="contact">
        PO Box 4471 Bronte Bay NSW 2099<br>
        0400 123 987 &nbsp;|&nbsp; info@brisko-coolworks.com.au<br>
        ABN: 12 345 678 901 &nbsp;|&nbsp; Licence No: 418829B
      </p>
      <svg class="diamonds" style="top:213px" viewBox="0 0 781 16">
        <g fill="none" stroke="#4fb9e3" stroke-width="2">
          <path d="M353 8 l5 -5 l5 5 l-5 5z"/>
          <path d="M385 8 l5 -5 l5 5 l-5 5z"/>
          <path d="M418 8 l5 -5 l5 5 l-5 5z"/>
        </g>
      </svg>
      <p class="website">WWW.BRISKO-COOLWORKS.COM.AU</p>
      <svg class="social" viewBox="0 0 781 26">
        <line x1="313" y1="13" x2="350" y2="13" stroke="#4fb9e3" stroke-width="1.5"/>
        <line x1="431" y1="13" x2="467" y2="13" stroke="#4fb9e3" stroke-width="1.5"/>
        <g fill="#333333">
          <circle cx="364" cy="13" r="11.5"/>
          <circle cx="390" cy="13" r="11.5"/>
          <circle cx="416" cy="13" r="11.5"/>
        </g>
      </svg>
    </section>
  </div>
</body>
</html>
```